Business card for Luxury Portable Restroom Trailer company

We are a Luxury Portable Restroom Trailer Company Called FALCRIDGE HIRES. Based in Orange County California. We provide portable restroom trailers for events, such as, Weddings, Concerts, Charity events, Sporting events, Tournaments, Corporate events, ect. We rent and Sell the Luxury restrooms. Our colors are white, grey, and Orange. As you will see in the logo we uploaded.
There are 2 people in the company so the names and titles will change for the 3 people but card will remain the same. Here is the information for each Person: Dwight Penner CFO 555 318-0476
next Person: Leon Marchetti VP 555 318-0476
Next Person: Owen Marchetti CEO 555 318-0476
Information to include on the card: Luxury Restroom Trailers Rental and Sales. Weddings, Concerts, Charity, Sporting and Corp. Events.

```html
<!DOCTYPE html>
<html lang="en">
<head>
<meta charset="UTF-8">
<title>Falcridge Hires – Business Card</title>
<link href="https://fonts.googleapis.com/css2?family=Montserrat:wght@500;700&family=Mulish:wght@500;600&display=swap" rel="stylesheet">
<style>
  :root {
    --orange: #f26b24;
    --white: #ffffff;
    --grey: #595b5e;
    --ink: #1d1d1d;
    --backdrop: #e9eaea;
  }
  * { margin: 0; padding: 0; box-sizing: border-box; }
  html, body {
    width: 1179px; height: 1200px; overflow: hidden;
    background: var(--backdrop);
  }
  .card {
    position: absolute; left: 221px;
    width: 738px; height: 423px;
    overflow: hidden;
  }
  .card--front { top: 161px; background: var(--white); }
  .card--back { top: 618px; background: var(--orange); }

  .brand-name {
    font-family: "Montserrat", sans-serif;
    font-weight: 700;
    letter-spacing: 1px;
    white-space: nowrap;
  }
  .card--front .brand-name {
    position: absolute; left: 36px; top: 44px;
    font-size: 29px; color: var(--grey);
  }

  .team { position: absolute; left: 36px; top: 124px; }
  .member { margin-bottom: 10px; }
  .member__name {
    font-family: "Montserrat", sans-serif; font-weight: 700;
    font-size: 24px; color: var(--orange); line-height: 28px;
  }
  .member__title, .member__phone {
    font-family: "Mulish", sans-serif; font-weight: 600;
    font-size: 19px; color: var(--ink); line-height: 26px;
  }
  .member__phone { display: flex; align-items: center; gap: 10px; }
  .phone-icon { width: 18px; height: 14px; }

  .accent-band {
    position: absolute; left: 506px; top: 0;
    width: 232px; height: 423px; background: var(--orange);
  }
  .emblem { position: absolute; left: 367px; top: 50px; width: 334px; height: 334px; }

  .card--back .brand-name {
    position: absolute; left: 0; right: 0; top: 138px;
    text-align: center; font-size: 50px; color: var(--white); letter-spacing: 2px;
  }
  .services {
    position: absolute; left: 0; right: 0; top: 318px;
    text-align: center;
    font-family: "Mulish", sans-serif; font-weight: 500;
    font-size: 19px; color: var(--white); line-height: 27px;
  }
  .services span { white-space: nowrap; }
  .services span::before {
    content: ""; display: inline-block;
    width: 11px; height: 11px; border-radius: 50%;
    background: var(--white); margin: 0 8px 2px 12px; vertical-align: middle;
  }
</style>
</head>
<body>

<section class="card card--front">
  <div class="brand-name">FALCRIDGE HIRES</div>

  <div class="team">
    <div class="member">
      <div class="member__name">DWIGHT PENNER</div>
      <div class="member__title">CFO</div>
      <div class="member__phone">
        <svg class="phone-icon" viewBox="0 0 18 14"><path d="M1 5 Q9 -1 17 5 L15 7 L12 6 L12 4 Q9 3 6 4 L6 6 L3 7 Z M4 7 L14 7 L16 14 L2 14 Z" fill="#f26b24"/></svg>
        555 318-0476
      </div>
    </div>
    <div class="member">
      <div class="member__name">LEON MARCHETTI</div>
      <div class="member__title">VP</div>
      <div class="member__phone">
        <svg class="phone-icon" viewBox="0 0 18 14"><path d="M1 5 Q9 -1 17 5 L15 7 L12 6 L12 4 Q9 3 6 4 L6 6 L3 7 Z M4 7 L14 7 L16 14 L2 14 Z" fill="#f26b24"/></svg>
        555 318-0476
      </div>
    </div>
    <div class="member">
      <div class="member__name">OWEN MARCHETTI</div>
      <div class="member__title">CEO</div>
      <div class="member__phone">
        <svg class="phone-icon" viewBox="0 0 18 14"><path d="M1 5 Q9 -1 17 5 L15 7 L12 6 L12 4 Q9 3 6 4 L6 6 L3 7 Z M4 7 L14 7 L16 14 L2 14 Z" fill="#f26b24"/></svg>
        555 318-0476
      </div>
    </div>
  </div>

  <div class="accent-band"></div>
  <svg class="emblem" viewBox="0 0 334 334" aria-hidden="true">
    <circle cx="167" cy="167" r="165" fill="#ffffff"/>
    <circle cx="167" cy="167" r="144" fill="none" stroke="#f26b24" stroke-width="15"/>
  </svg>
</section>

<section class="card card--back">
  <div class="brand-name">FALCRIDGE HIRES</div>
  <div class="services">
    <div><span>Luxury Restroom Trailers Rental and Sales</span></div>
    <div><span>Weddings</span><span>Concerts</span><span>Charity</span><span>Sporting and Corp</span><span>Events</span></div>
  </div>
</section>

</body>
</html>
```